Tavenhurst Falcons FC Website

We are looking to develop a new website for Tavenhurst FC. Tavenhurst FC has now joined with Tavenhurst Falcons FC and we are looking at a website that can work for both clubs. Tavenhurst FC play in a local park football competition while tavenhurst Falcons are a Semi Professional team that plays in the Ostral Premier Series Competition. What we are after is two separate website off the one platform. I have attached both team logos for you to visualise. Also you can look at the existing tavenhurst website www.tavenhurstfc.net.au. We are looking for a huge improvement in the website and it will be imperative we have links to sponsors and the sponsors can get regular visuals. Weare looking to move this club forward and have a very professional website that can communicate clearly with the community.

Hi All,

Please remember that the website is to represent two clubs;
1. Tavenhurst Falcons FC (Competes in Semi Professional League)
2. Tavenhurst FC (Compete in KPWLT League which is a lower level)

Further to this the Tavenhurst Falcons FC page will require a player profile page which will show photos of each player and a little bio on each.

Thanks

Reason: Would like to spend more time review existing and new designs

```html
<!DOCTYPE html>
<html lang="en">
<head>
<meta charset="utf-8">
<title>Club Awards – Tavenhurst FC</title>
<link rel="stylesheet" href="https://fonts.googleapis.com/css2?family=Roboto+Condensed:wght@400;700&family=Libre+Baskerville:ital,wght@0,400;0,700;1,400&family=Arimo:wght@400;700&display=swap">
<style>
:root{
  --red:#e3282b;
  --red-dark:#b51d1f;
  --red-deep:#8f1416;
  --white:#ffffff;
  --ink:#1d1d1d;
  --grey-bg:#efefef;
  --grey-line:#d4d4d4;
  --grey-mid:#9a9a9a;
  --gold:#e6b321;
  --green:#5aa83a;
  --night:#0d0b12;
}
*{box-sizing:border-box;margin:0;padding:0}
html,body{width:1200px;height:3008px;overflow:hidden}
body{position:relative;background:var(--grey-bg);font-family:"Arimo",Arial,sans-serif;color:var(--ink)}

/* top utility bar */
.utility-bar{position:absolute;left:0;top:0;width:1200px;height:60px;background:var(--red-dark);color:var(--white);font:700 15px "Roboto Condensed",sans-serif;text-transform:uppercase}
.utility-bar span{position:absolute;top:20px}
.utility-join{left:148px}
.utility-tickets{left:333px}
.utility-follow{left:733px}
.social-list{position:absolute;left:840px;top:17px;display:flex;gap:14px}
.social-list i{display:block;width:24px;height:24px;background:var(--white);opacity:.85;border-radius:4px}

/* main nav */
.main-nav{position:absolute;left:0;top:60px;width:1200px;height:96px;background:var(--red);font:700 24px "Roboto Condensed",sans-serif;color:var(--white)}
.main-nav a{position:absolute;top:28px;color:var(--white);text-decoration:none}
.main-nav .is-active{top:0;height:96px;padding:28px 18px 0;background:var(--red-dark)}
.nav-search{position:absolute;left:1118px;top:80px}

.club-mark{position:absolute;left:520px;top:0;width:160px;height:174px;background:var(--white);display:flex;flex-direction:column;align-items:center;justify-content:center;gap:10px;box-shadow:0 4px 10px rgba(0,0,0,.25)}
.club-mark i{display:block;width:70px;height:70px;border-radius:50%;background:var(--red)}
.club-mark b{font:700 20px "Roboto Condensed",sans-serif;color:var(--red);text-align:center;line-height:1.05}

/* hero */
.hero{position:absolute;left:0;top:156px;width:1200px;height:630px;
  background:
   radial-gradient(circle at 1020px 130px,rgba(235,170,90,.55),transparent 190px),
   radial-gradient(circle at 260px 110px,rgba(230,120,80,.45),transparent 170px),
   radial-gradient(circle at 620px 420px,rgba(240,190,90,.35),transparent 320px),
   radial-gradient(ellipse at 600px 600px,rgba(200,150,60,.5),transparent 500px),
   linear-gradient(180deg,var(--night) 0%,#231a1e 55%,#4a3318 100%)}
.hero-menu{position:absolute;left:0;top:42px;list-style:none}
.hero-menu li{height:54px;margin-bottom:24px;padding:12px 16px 0 14px;font:italic 700 23px "Libre Baskerville",serif;color:var(--white);background:var(--red);width:max-content}
.hero-menu li.is-muted{background:#cfcfcf;color:var(--ink)}
.hero-menu li:nth-child(1){width:322px}
.hero-menu li:nth-child(3){width:190px}
.medal{position:absolute;left:549px;top:213px}
.hero-title{position:absolute;left:0;top:306px;width:1200px;text-align:center;font:italic 44px "Libre Baskerville",serif;color:var(--white)}

/* section intro */
.intro{position:absolute;left:0;top:786px;width:1200px;height:280px;background:#f6f6f6}
.intro-dots{position:absolute;left:0;top:36px;width:1200px;text-align:center;font:700 30px Arial,sans-serif;letter-spacing:6px;line-height:1}
.intro-rule{position:absolute;top:113px;height:1px;background:var(--grey-line)}
.intro h2{position:absolute;left:0;top:95px;width:1200px;text-align:center;font:italic 700 28px "Libre Baskerville",serif;text-transform:uppercase}
.intro p{position:absolute;left:0;top:136px;width:1200px;text-align:center;font:italic 16px "Libre Baskerville",serif}

/* award entries */
.award{position:absolute;left:0;width:1200px;height:470px}
.award-photo{position:absolute;left:93px;top:80px;width:252px;height:252px;border-radius:50%;border:12px solid #dedede;box-shadow:0 3px 8px rgba(0,0,0,.2)}
.photo-senior{background:radial-gradient(circle at 50% 40%,#6b6464,#1e1d22 70%)}
.photo-person{background:radial-gradient(circle at 50% 45%,#7d8fb5,#21306e 70%)}
.photo-team{background:linear-gradient(180deg,#6d84b0 0%,#1b2c6a 45%,#7a1c2a 100%)}
.award-name{position:absolute;left:99px;top:328px;width:255px;height:48px;background:var(--red);color:var(--white);font:italic 700 19px "Libre Baskerville",serif;padding:12px 0 0 18px;clip-path:polygon(0 0,92% 0,100% 50%,92% 100%,0 100%)}
.award-name::before{content:"";position:absolute}
.award-icon{position:absolute;width:78px;height:78px;border-radius:50%;background:var(--white);border:3px solid #cdcdcd;display:flex;align-items:center;justify-content:center}
.icon-trophy{left:351px;top:41px}
.icon-shirt{left:399px;top:155px}
.icon-calendar{left:360px;top:269px}
.award-stat{position:absolute;left:435px;top:50px;height:66px;width:309px;background:var(--red);border-radius:0 33px 33px 0;color:var(--white);font:italic 26px "Libre Baskerville",serif;padding:14px 0 0 20px}
.award-stat b{display:inline-block;border:2px solid var(--white);padding:0 6px;margin-right:10px;font-style:normal;font-weight:400}
.award h3{position:absolute;left:519px;top:130px;font:italic 34px "Libre Baskerville",serif;text-transform:uppercase;letter-spacing:.5px}
.award p{position:absolute;left:519px;top:173px;width:596px;font:19.5px/24px "Arimo",Arial,sans-serif;text-align:justify}
.separator{position:absolute;left:384px;width:516px;height:2px;background:var(--grey-line)}

/* pagination */
.pagination{position:absolute;left:444px;top:2553px;display:flex;gap:9px;list-style:none}
.pagination li{width:54px;height:54px;border-radius:50%;border:2px solid #bbb;background:var(--white);text-align:center;font:27px/50px "Libre Baskerville",serif}
.pagination .is-current{background:var(--red);border-color:var(--red);color:var(--white)}

/* footer */
.site-footer{position:absolute;left:0;top:2694px;width:1200px;height:276px;border-top:6px solid var(--red);background:linear-gradient(180deg,#f4f4f4 0%,#e9e9e9 60%,#d6d6d6 100%)}
.footer-col{position:absolute;top:60px}
.footer-col h4{font:700 29px "Roboto Condensed",sans-serif;text-transform:uppercase;padding-bottom:6px;border-bottom:3px solid var(--grey-mid)}
.footer-col ul{list-style:none;margin-top:12px;font:23px/29px "Roboto Condensed",sans-serif;color:#333}
.footer-icon{position:absolute;top:-18px}
.col-home{left:150px;width:124px}
.col-club{left:402px;width:124px}
.col-fixtures{left:651px;width:452px}
.col-fixtures ul{display:grid;grid-template-columns:1fr auto}
.copyright{position:absolute;left:0;top:2970px;width:1200px;height:38px;background:var(--red);color:var(--white);font:14px/38px "Arimo",Arial,sans-serif;padding-left:150px}
</style>
</head>
<body>

<header>
  <div class="utility-bar">
    <span class="utility-join">Join us now ▸</span>
    <span class="utility-tickets">Get your tickets ▸</span>
    <span class="utility-follow">Follow us :</span>
    <div class="social-list"><i></i><i></i><i></i><i></i><i></i></div>
  </div>
  <nav class="main-nav">
    <a style="left:42px">Home</a>
    <a style="left:148px">Photo Gallery</a>
    <a style="left:318px">Fixture &amp; Results</a>
    <a style="left:701px">News</a>
    <a style="left:796px">Sponsor</a>
    <a class="is-active" style="left:886px">Club</a>
    <a style="left:986px">Contact Us</a>
    <svg class="nav-search" width="28" height="28" viewBox="0 0 28 28" style="top:24px"><circle cx="11" cy="11" r="8" fill="none" stroke="#fff" stroke-width="3.5"/><line x1="17" y1="17" x2="25" y2="25" stroke="#fff" stroke-width="4" stroke-linecap="round"/></svg>
  </nav>
  <div class="club-mark"><i></i><b>Tavenhurst<br>FC</b></div>
</header>

<section class="hero" role="img" aria-label="Night photograph of a city skyline and stadium with fireworks bursting overhead">
  <ul class="hero-menu">
    <li class="is-muted">Tavenhurst FC History</li>
    <li>Committee Members</li>
    <li class="is-muted">Club Awards</li>
    <li>Club Forms</li>
  </ul>
  <svg class="medal" width="102" height="102" viewBox="0 0 102 102">
    <circle cx="51" cy="51" r="51" fill="#e3282b"/>
    <path d="M38 22 L46 46 L56 46 L64 22 Z" fill="#fff"/>
    <circle cx="51" cy="62" r="18" fill="#fff"/>
    <circle cx="51" cy="62" r="12" fill="#e3282b"/>
    <text x="51" y="68" text-anchor="middle" font-family="Arimo,Arial,sans-serif" font-weight="700" font-size="16" fill="#fff">1</text>
  </svg>
  <h1 class="hero-title">• Club Awards •</h1>
</section>

<section class="intro">
  <div class="intro-dots">•••</div>
  <div class="intro-rule" style="left:0;width:270px"></div>
  <div class="intro-rule" style="left:930px;width:270px"></div>
  <h2>Our awards recipients for this year</h2>
  <p>Congratulations!</p>
</section>

<svg width="0" height="0" style="position:absolute">
  <defs>
    <symbol id="i-trophy" viewBox="0 0 40 40"><path d="M12 6h16v10a8 8 0 0 1-16 0z" fill="#333"/><path d="M12 9H6a6 6 0 0 0 6 8M28 9h6a6 6 0 0 1-6 8" fill="none" stroke="#333" stroke-width="2.5"/><rect x="18" y="23" width="4" height="7" fill="#333"/><rect x="12" y="30" width="16" height="4" fill="#333"/></symbol>
    <symbol id="i-shirt" viewBox="0 0 40 40"><path d="M14 5l-9 5 3 8 4-2v19h16V16l4 2 3-8-9-5a6 6 0 0 1-12 0z" fill="none" stroke="#333" stroke-width="2.5" stroke-linejoin="round"/><path d="M17 12v20M20 12v20M23 12v20" stroke="#333" stroke-width="2"/></symbol>
    <symbol id="i-calendar" viewBox="0 0 40 40"><rect x="6" y="9" width="28" height="25" rx="2" fill="none" stroke="#333" stroke-width="2.5"/><rect x="6" y="9" width="28" height="6" fill="#333"/><line x1="13" y1="5" x2="13" y2="12" stroke="#333" stroke-width="3"/><line x1="27" y1="5" x2="27" y2="12" stroke="#333" stroke-width="3"/><g fill="#333"><rect x="10" y="19" width="4" height="4"/><rect x="18" y="19" width="4" height="4"/><rect x="26" y="19" width="4" height="4"/><rect x="10" y="26" width="4" height="4"/><rect x="18" y="26" width="4" height="4"/><rect x="26" y="26" width="4" height="4"/></g></symbol>
  </defs>
</svg>

<main>
  <article class="award" style="top:1000px">
    <div class="award-photo photo-senior" role="img" aria-label="Portrait photograph of the senior player of the year in club kit"></div>
    <div class="award-name">Daniel Whitcombe</div>
    <div class="award-icon icon-trophy"><svg width="42" height="42"><use href="#i-trophy"/></svg></div>
    <div class="award-icon icon-shirt"><svg width="42" height="42"><use href="#i-shirt"/></svg></div>
    <div class="award-icon icon-calendar"><svg width="42" height="42"><use href="#i-calendar"/></svg></div>
    <div class="award-stat"><b>35</b>Goals this Season</div>
    <h3>Senior Player of the Year 2013</h3>
    <p>Daniel is a very dedicated and kind person that does everything from his heart. He managers two teams and is always there for the children. On game days he comes in and helps on the BBQ around the grounds without being asked. We are proud to have Daniel in our Tavenhurst FC family.</p>
  </article>

  <div class="separator" style="top:1479px"></div>

  <article class="award" style="top:1534px">
    <div class="award-photo photo-person" role="img" aria-label="Portrait photograph of the club person of the year holding a match ball"></div>
    <div class="award-name">Peter (Pete) Lorant</div>
    <div class="award-icon icon-trophy"><svg width="42" height="42"><use href="#i-trophy"/></svg></div>
    <div class="award-icon icon-shirt"><svg width="42" height="42"><use href="#i-shirt"/></svg></div>
    <div class="award-icon icon-calendar"><svg width="42" height="42"><use href="#i-calendar"/></svg></div>
    <h3>Club Person Year 2013</h3>
    <p>Daniel is a very dedicated and kind person that does everything from his heart. He managers two teams and is always there for the children. On game days he comes in and helps on the BBQ around the grounds without being asked. We are proud to have Daniel in our Tavenhurst FC family.</p>
  </article>

  <div class="separator" style="top:2004px"></div>

  <article class="award" style="top:2065px">
    <div class="award-photo photo-team" role="img" aria-label="Team photograph of the squad of the year lined up in kit"></div>
    <div class="award-name">Peter (Pete) Lorant</div>
    <div class="award-icon icon-trophy"><svg width="42" height="42"><use href="#i-trophy"/></svg></div>
    <div class="award-icon icon-shirt"><svg width="42" height="42"><use href="#i-shirt"/></svg></div>
    <div class="award-icon icon-calendar"><svg width="42" height="42"><use href="#i-calendar"/></svg></div>
    <h3>Team of the Year 2013</h3>
    <p>Daniel is a very dedicated and kind person that does everything from his heart. He managers two teams and is always there for the children. On game days he comes in and helps on the BBQ around the grounds without being asked. We are proud to have Daniel in our Tavenhurst FC family.</p>
  </article>

  <ul class="pagination">
    <li>1</li><li class="is-current">2</li><li>3</li><li>4</li><li>5</li>
  </ul>
</main>

<footer class="site-footer">
  <div class="footer-col col-home">
    <svg class="footer-icon" style="left:-72px" width="56" height="64" viewBox="0 0 40 46"><path d="M10 2h20v14a10 10 0 0 1-20 0z" fill="#e6b321"/><path d="M10 6H3a7 7 0 0 0 8 9M30 6h7a7 7 0 0 1-8 9" fill="none" stroke="#e6b321" stroke-width="3"/><rect x="17" y="25" width="6" height="9" fill="#e6b321"/><rect x="10" y="34" width="20" height="6" fill="#c9961a"/></svg>
    <h4>Home</h4>
    <ul><li>News</li><li>Gallery</li><li>Sponsor</li><li>Contact Us</li></ul>
  </div>
  <div class="footer-col col-club">
    <svg class="footer-icon" style="left:-76px" width="60" height="60" viewBox="0 0 40 40"><circle cx="20" cy="20" r="18" fill="#fff" stroke="#222" stroke-width="2.5"/><path d="M20 12l7 5-3 8h-8l-3-8z" fill="#222"/></svg>
    <h4>Club</h4>
    <ul><li>History</li><li>Committee</li><li>Awards</li><li>Forms</li></ul>
  </div>
  <div class="footer-col col-fixtures">
    <svg class="footer-icon" style="left:-78px" width="66" height="56" viewBox="0 0 44 36"><path d="M2 30L10 4h24l8 26z" fill="#5aa83a"/><path d="M22 4v26M6 17h32" stroke="#fff" stroke-width="1.5"/></svg>
    <h4>Fixtures &amp; Results</h4>
    <ul>
      <li>Premier League</li><li>Under 10 / 2</li>
      <li>Premier League</li><li>Under 10 / 3</li>
      <li>ResSuper League</li><li>Under 11 / 1</li>
      <li>Super League Res</li><li>Under 12 / 3</li>
    </ul>
  </div>
</footer>
<div class="copyright">© 2012-2015 All Rights Reserved to Tavenhurst Falcons FC</div>

</body>
</html>
```